Equipment Finance Specialist I work with companies who need the funds to buy their equipment

I would like a business card that stands out on the shelves. I want to be able to hand it to someone and say WOW. This card should have my logo.
You can put color into it I am very open on design and color

What my company does is we deal with dealerships that sell equipment such as Dump Trucks garbage trucks tractors trailers. Customers get referred to us and depending on their time in business we will ask for the following items

Companies that have been in business for more than two years we have a credit application program up to 250K . With this program we need the following items Credit application filled out(which is what I would like to be able for the customer to click on my website to get.) as well as three current month bank statements.

Deals over 250k we will need the following items

2 years business tax returns
2 years personal tax returns
Profit & Loss statement
Personal Financial Statement

what we do
100% FINANCING
SEASONAL PAYMENTS
LOAN BALLOON PAYMENTS
TRAC LEASING
LOW-INTEREST REFINANCING RATES
DEBT CONSOLIDATION

We specialize in creative financing solutions and offer a variety of reliable, flexible and expandable lending choices.

Target Market(s)

Trucking Companies

Industry/Entity Type

Trucking Company

Contact Information for Business Card

* $250,000 Application only Program
* Loans from $30,000 to 5,000,000
* Competitive Interest Rates

Font styles to use
Serif
Sans Serif

Colors

Designer to choose colors to be used in the design.

Requirements
Must have
• On the back of the card.
• * $250,000 Application only Program
• * Loans from $30,000 to 5,000,000
• My name, email, website. address
• * Competitive Interest Rates
• * 100% Financing
Nice to have
• I want my logo to pop on the card
• My logo is the great one I would like to use
Should not have
• I am up for your creativity as well

```html
<!DOCTYPE html>
<html lang="en">
<head>
<meta charset="utf-8">
<title>Ironline Funding – Business Card</title>
<link href="https://fonts.googleapis.com/css2?family=Work+Sans:wght@400;500;700;800&display=swap" rel="stylesheet">
<style>
  :root {
    --navy: #1c2f6e;
    --navy-deep: #14245a;
    --red: #e0202f;
    --white: #ffffff;
    --paper: #f4f5f8;
    --stage: #d9dbe0;
    --ink: #1c2f6e;
    --soft-white: rgba(255, 255, 255, 0.88);
  }
  * { box-sizing: border-box; margin: 0; padding: 0; }
  html, body {
    width: 1200px; height: 900px; overflow: hidden;
    background: var(--stage);
    font-family: "Work Sans", Arial, sans-serif;
  }
  .sheet {
    width: 1200px; height: 900px;
    display: flex; flex-direction: column;
    align-items: center; justify-content: center; gap: 40px;
  }
  .card {
    width: 700px; height: 400px;
    border-radius: 22px;
    position: relative; overflow: hidden;
    box-shadow: 0 10px 30px rgba(20, 36, 90, 0.22);
  }

  /* Front */
  .card-front { background: linear-gradient(135deg, var(--white), var(--paper)); }
  .truck-art {
    position: absolute; left: 0; top: 0; bottom: 0; width: 330px;
    background: linear-gradient(160deg, var(--navy) 0%, var(--navy-deep) 100%);
    border-radius: 0 60% 0 0 / 0 100% 0 0;
  }
  .front-content {
    position: absolute; right: 40px; top: 40px; bottom: 36px;
    display: flex; flex-direction: column; align-items: flex-end; text-align: right;
    color: var(--ink);
  }
  .brand { display: flex; align-items: center; gap: 12px; }
  .brand-dot {
    width: 44px; height: 44px; border-radius: 50%;
    background: var(--navy); flex: none;
  }
  .brand-name {
    font-weight: 800; font-size: 30px; letter-spacing: 1px;
    text-transform: uppercase; color: var(--navy); line-height: 1;
  }
  .person-name {
    margin-top: 40px;
    font-size: 28px; font-weight: 500; letter-spacing: 1px;
    text-transform: uppercase; color: var(--red);
  }
  .person-role { font-size: 17px; margin-top: 2px; }
  .address { margin-top: 20px; font-size: 17px; line-height: 1.4; }
  .contact-list { margin-top: auto; list-style: none; font-size: 17px; line-height: 1.6; }
  .contact-list li { display: flex; align-items: center; justify-content: flex-end; gap: 8px; }
  .contact-list svg { width: 14px; height: 14px; flex: none; }
  .web-accent { color: var(--red); }

  /* Back */
  .card-back {
    background: linear-gradient(150deg, var(--navy) 0%, var(--navy-deep) 100%);
    display: flex; flex-direction: column; align-items: center; justify-content: center;
    gap: 34px;
  }
  .card-back .brand { gap: 18px; }
  .card-back .brand-dot { width: 64px; height: 64px; background: var(--white); }
  .card-back .brand-name { color: var(--white); font-size: 44px; }
  .program-list {
    list-style: none;
    display: grid; grid-template-columns: auto auto; column-gap: 44px; row-gap: 12px;
    color: var(--soft-white); font-size: 17px; font-weight: 500;
  }
  .program-list li { display: flex; align-items: center; gap: 10px; }
  .program-list li::before {
    content: ""; width: 8px; height: 8px; border-radius: 50%;
    background: var(--red); flex: none;
  }
</style>
</head>
<body>
<main class="sheet">

  <section class="card card-front">
    <div class="truck-art" role="img" aria-label="Navy and white illustration of a heavy truck front with stars"></div>
    <div class="front-content">
      <div class="brand">
        <span class="brand-dot"></span>
        <span class="brand-name">Ironline Funding</span>
      </div>
      <p class="person-name">Daniel Reyes</p>
      <p class="person-role">Director</p>
      <p class="address">1820 Harrow Ridge Dr.<br>Frisco, TX 75033</p>
      <ul class="contact-list">
        <li><span>1300 412 667</span>
          <svg viewBox="0 0 24 24" fill="none" stroke="#e0202f" stroke-width="2.4"><path d="M5 3h4l2 5-2.5 1.5a11 11 0 0 0 6 6L16 13l5 2v4a2 2 0 0 1-2 2A17 17 0 0 1 3 5a2 2 0 0 1 2-2z"/></svg>
        </li>
        <li><span>hello@ironlinefunding.com</span>
          <svg viewBox="0 0 24 24" fill="none" stroke="#e0202f" stroke-width="2.4"><rect x="3" y="5" width="18" height="14" rx="2"/><path d="M3 7l9 6 9-6"/></svg>
        </li>
        <li><span>www.<span class="web-accent">ironlinefunding</span>.com</span>
          <svg viewBox="0 0 24 24" fill="none" stroke="#e0202f" stroke-width="2.4"><circle cx="12" cy="12" r="9"/><path d="M3 12h18M12 3c3 3 3 15 0 18M12 3c-3 3-3 15 0 18"/></svg>
        </li>
      </ul>
    </div>
  </section>

  <section class="card card-back">
    <div class="brand">
      <span class="brand-dot"></span>
      <span class="brand-name">Ironline Funding</span>
    </div>
    <ul class="program-list">
      <li>$250,000 Application Only Program</li>
      <li>Loans from $30,000 to $5,000,000</li>
      <li>Competitive Interest Rates</li>
      <li>100% Financing</li>
    </ul>
  </section>

</main>
</body>
</html>
```